Sales presentation introduction for Finance and Tech firms

Our business is two fold - 1) recruitment 2) consultancy. We would like a one or two page template that we can use to send to potential clients. The template will ideally be the same for the recruitment and consultancy side. We need to be able to edit the template to enter text.

I have attached our logo so you can see what we currently use on Corvella.

Sector is financial services and technology. We do not intent to have lots of text but the layout/images/designs to be used should cover some of page in a way that it takes up some space to avoid having to write lot of text.

Open to colour suggestions.

Please look at the attached word doc to see the text I would like for the two presentations.

Happy to answer questions.

Target Market(s)

Directors

Industry/Entity Type

Finance and tech companies

Colors
0094D4
00A9DD
6FCCEA
C7EBF8
E9F6FB

Requirements
Must have
• Editable text

```html
<!DOCTYPE html>
<html lang="en">
<head>
<meta charset="utf-8">
<title>Meridian K2 – Sales Introduction Sheets</title>
<link href="https://fonts.googleapis.com/css2?family=Hind:wght@400;500;600;700&display=swap" rel="stylesheet">
<style>
:root{
  --stage:#a6a6a6;
  --paper:#ffffff;
  --ink:#1d1d1b;
  --brand:#1f7cc4;
  --brand-dark:#0f56a3;
  --brand-light:#6fccea;
  --tint:#e4f4fd;
  --footer:#231f20;
  --sky-a:#dcecf8;
  --sky-b:#5d8fc0;
  --net-a:#0b1a33;
  --net-b:#2a4f7d;
}
*{box-sizing:border-box;margin:0;padding:0}
html,body{width:958px;height:1200px;overflow:hidden}
body{background:var(--stage);font-family:"Hind",sans-serif;color:var(--ink);position:relative}

.sheet{position:absolute;width:377px;height:532px;overflow:hidden;background:var(--paper)}
.sheet--tl{left:82px;top:58px}
.sheet--tr{left:493px;top:58px}
.sheet--bl{left:82px;top:623px}
.sheet--br{left:493px;top:623px}
.sheet__inner{position:absolute;left:0;top:0;width:678px;height:957px;transform:scale(0.556);transform-origin:0 0}

.hero-shapes{position:absolute;left:0;top:0}
.hero-photo{position:absolute;left:0;top:0;width:678px;height:413px;
  clip-path:polygon(247px 0,678px 0,678px 240px,564px 413px)}
.hero-photo--city{background:linear-gradient(160deg,var(--sky-b) 0%,#9cc3e6 35%,var(--sky-a) 60%,#7fa9d3 100%)}
.hero-photo--network{background:radial-gradient(circle at 78% 38%,#6fa7d8 0%,var(--net-b) 22%,var(--net-a) 65%)}

.brand-name{position:absolute;left:40px;top:96px;font-size:31px;font-weight:500;letter-spacing:1.5px;color:var(--ink);line-height:1}
.tagline{position:absolute;left:40px;top:156px;color:#fff;font-size:17.5px;font-weight:700;line-height:22px;z-index:2}
.tagline span{display:block;white-space:nowrap}

.section-title{position:absolute;left:40px;font-size:16.5px;font-weight:700;letter-spacing:.2px;line-height:1}
.intro{position:absolute;left:40px;width:440px;font-size:9.2px;line-height:12.3px;text-align:justify}
.intro p+p{margin-top:8px}

.service-grid{position:absolute;left:40px;width:610px;display:grid;grid-template-columns:220px 227px 160px;row-gap:14px}
.service{display:flex;align-items:center;gap:17px;height:61px}
.service svg{flex:none}
.service span{font-size:12.5px;line-height:16.5px}

.capabilities{position:absolute;left:0;top:657px;width:678px;height:255px;background:var(--tint)}
.capability{position:absolute;width:290px;padding-left:72px}
.capability svg{position:absolute;left:0;top:0}
.capability h3{font-size:14.5px;font-weight:600;color:var(--brand-dark);line-height:1;margin-bottom:4px}
.capability p{font-size:8.6px;line-height:12.2px;text-align:justify;width:210px}

.contact-bar{position:absolute;left:0;top:912px;width:678px;height:45px;background:var(--footer);color:#fff;
  display:flex;align-items:center;padding-left:40px;gap:20px;font-size:14.5px;letter-spacing:.3px}
.contact-bar span{display:flex;align-items:center;gap:7px}

.recruit-intro{position:absolute;left:40px;top:330px;width:436px;font-size:12.2px;line-height:15px;text-align:justify}
.recruit-intro .lead{color:var(--brand-dark)}
.recruit-intro p+p{margin-top:5px}
.recruit-col{position:absolute;top:462px;font-size:9.4px;line-height:12.4px;text-align:justify}
.recruit-col--left{left:40px;width:278px;font-weight:500}
.recruit-col--right{left:354px;width:285px}
.ticks{list-style:none;margin-top:8px}
.ticks li{position:relative;padding-left:13px;margin-bottom:8px;font-size:9.6px}
.ticks li::before{content:"";position:absolute;left:0;top:3px;width:7px;height:7px;border-radius:50%;background:var(--brand)}
.ticks--pairs{display:grid;grid-template-columns:148px 130px;column-gap:10px;margin-top:8px}
.ticks--pairs li{font-size:9px;line-height:11.6px;text-align:left;margin-bottom:8px}
.recruit-close{position:absolute;left:40px;top:644px;width:598px;font-size:9.8px;line-height:13px;text-align:justify}
</style>
</head>
<body>

<svg width="0" height="0" style="position:absolute" aria-hidden="true">
  <defs>
    <symbol id="svc-doc" viewBox="0 0 62 62">
      <circle cx="31" cy="31" r="30" fill="#1f7cc4"/>
      <circle cx="31" cy="31" r="25" fill="none" stroke="#fff" stroke-width="1.4"/>
      <rect x="22" y="18" width="18" height="24" rx="2" fill="none" stroke="#fff" stroke-width="1.6"/>
      <path d="M26 25h10M26 30h10M26 35h6" stroke="#fff" stroke-width="1.6"/>
    </symbol>
    <symbol id="svc-chart" viewBox="0 0 62 62">
      <circle cx="31" cy="31" r="30" fill="#1f7cc4"/>
      <circle cx="31" cy="31" r="25" fill="none" stroke="#fff" stroke-width="1.4"/>
      <path d="M20 42h22M23 41v-6M29 41v-10M35 41v-14M41 41v-18" stroke="#fff" stroke-width="2"/>
      <path d="M21 30l8-7 5 4 9-8" fill="none" stroke="#fff" stroke-width="1.4"/>
    </symbol>
    <symbol id="svc-search" viewBox="0 0 62 62">
      <circle cx="31" cy="31" r="30" fill="#1f7cc4"/>
      <circle cx="31" cy="31" r="25" fill="none" stroke="#fff" stroke-width="1.4"/>
      <circle cx="28" cy="28" r="8" fill="none" stroke="#fff" stroke-width="1.8"/>
      <path d="M34 34l8 8" stroke="#fff" stroke-width="2.4"/>
    </symbol>
    <symbol id="cap-gear" viewBox="0 0 60 60">
      <circle cx="30" cy="32" r="17" fill="none" stroke="#0f56a3" stroke-width="2" stroke-dasharray="6 3"/>
      <circle cx="30" cy="32" r="11" fill="none" stroke="#0f56a3" stroke-width="2"/>
      <rect x="24" y="28" width="12" height="9" rx="1" fill="none" stroke="#0f56a3" stroke-width="1.8"/>
      <path d="M6 14v-8M11 14v-5M16 14v-9M52 10l5-5" stroke="#0f56a3" stroke-width="2"/>
    </symbol>
    <symbol id="cap-bulb" viewBox="0 0 60 60">
      <circle cx="18" cy="16" r="11" fill="none" stroke="#0f56a3" stroke-width="2"/>
      <path d="M13 30h10M14 34h8" stroke="#0f56a3" stroke-width="2"/>
      <circle cx="44" cy="44" r="9" fill="none" stroke="#0f56a3" stroke-width="2" stroke-dasharray="5 2.5"/>
      <circle cx="44" cy="44" r="4" fill="none" stroke="#0f56a3" stroke-width="2"/>
      <path d="M40 8h6v14M43 19l3 3 3-3M8 54v-10M5 47l3-3 3 3M12 54h14" fill="none" stroke="#0f56a3" stroke-width="1.8"/>
    </symbol>
    <symbol id="cap-laptop" viewBox="0 0 60 60">
      <rect x="6" y="20" width="40" height="26" rx="2" fill="none" stroke="#0f56a3" stroke-width="2"/>
      <path d="M2 50h50" stroke="#0f56a3" stroke-width="2.4"/>
      <circle cx="38" cy="18" r="12" fill="#e4f4fd" stroke="#0f56a3" stroke-width="2" stroke-dasharray="6 3"/>
      <circle cx="38" cy="18" r="6" fill="none" stroke="#0f56a3" stroke-width="2"/>
    </symbol>
    <symbol id="cap-org" viewBox="0 0 60 60">
      <circle cx="30" cy="14" r="12" fill="none" stroke="#0f56a3" stroke-width="2"/>
      <circle cx="30" cy="11" r="4" fill="none" stroke="#0f56a3" stroke-width="1.8"/>
      <path d="M23 21c2-4 12-4 14 0" fill="none" stroke="#0f56a3" stroke-width="1.8"/>
      <path d="M30 26v10M10 36h40M10 36v8M30 36v8M50 36v8" fill="none" stroke="#0f56a3" stroke-width="2"/>
      <rect x="5" y="44" width="10" height="9" fill="none" stroke="#0f56a3" stroke-width="2"/>
      <rect x="25" y="44" width="10" height="9" fill="none" stroke="#0f56a3" stroke-width="2"/>
      <rect x="45" y="44" width="10" height="9" fill="none" stroke="#0f56a3" stroke-width="2"/>
    </symbol>
    <symbol id="ico-phone" viewBox="0 0 22 22">
      <circle cx="11" cy="11" r="10" fill="none" stroke="#fff" stroke-width="1.3"/>
      <path d="M7.5 6.5l2 0 1 2.5-1.2 1a6 6 0 0 0 2.7 2.7l1-1.2 2.5 1v2a1 1 0 0 1-1 1A8 8 0 0 1 6.5 7.5a1 1 0 0 1 1-1z" fill="#fff"/>
    </symbol>
    <symbol id="ico-mail" viewBox="0 0 22 22">
      <circle cx="11" cy="11" r="10" fill="none" stroke="#fff" stroke-width="1.3"/>
      <rect x="6" y="7.5" width="10" height="7" fill="none" stroke="#fff" stroke-width="1.2"/>
      <path d="M6 7.5l5 4 5-4" fill="none" stroke="#fff" stroke-width="1.2"/>
    </symbol>
    <symbol id="ico-web" viewBox="0 0 22 22">
      <circle cx="11" cy="11" r="10" fill="none" stroke="#fff" stroke-width="1.3"/>
      <circle cx="11" cy="11" r="5.5" fill="none" stroke="#fff" stroke-width="1.1"/>
      <ellipse cx="11" cy="11" rx="2.3" ry="5.5" fill="none" stroke="#fff" stroke-width="1.1"/>
      <path d="M5.5 11h11" stroke="#fff" stroke-width="1.1"/>
    </symbol>
  </defs>
</svg>

<!-- ===== Consultancy sheet, city variant ===== -->
<section class="sheet sheet--tl">
  <div class="sheet__inner">
    <svg class="hero-shapes" width="678" height="430" viewBox="0 0 678 430" aria-hidden="true">
      <polygon points="238,0 678,0 678,226 566,428" fill="var(--brand-dark)"/>
      <polygon points="600,413 678,413 678,300" fill="var(--brand-light)"/>
      <polygon points="0,138 330,138 440,282 0,282" fill="var(--brand)"/>
    </svg>
    <div class="hero-photo hero-photo--city" role="img" aria-label="Upward view of glass office skyscrapers against a blue sky"></div>
    <div class="brand-name">MERIDIAN K2</div>
    <p class="tagline"><span>A partner who brings new and</span><span>innovative ideas to the table, through</span><span>extensive industry experience and</span><span>knowledge. Meridian will ensure you are</span><span>prepared for growth.</span></p>
    <h2 class="section-title" style="top:296px">MERIDIAN CONSULTANCY</h2>
    <div class="intro" style="top:316px">
      <p>Meridian K2 is a bespoke consultancy firm that specialises in buy side investment. Through an industry based consultative approach we assist our clients in preparing for, and facilitating, long term growth. Working closely with our clients we combine innovative thinking and breakthrough technologies to accelerate progress and, together, achieve enduring results.</p>
      <p>Experienced in successfully delivering change for global organisations as well as assisting smaller firms during their growth phase. Meridian will work with you create a workable model and ensure successful delivery of the project.</p>
    </div>
    <div class="service-grid" style="top:431px">
      <div class="service"><svg width="61" height="61"><use href="#svc-doc"/></svg><span>Order<br>Management<br>and Trading</span></div>
      <div class="service"><svg width="61" height="61"><use href="#svc-doc"/></svg><span>CRM/ Onboarding</span></div>
      <div class="service"><svg width="61" height="61"><use href="#svc-doc"/></svg><span>Compliance</span></div>
      <div class="service"><svg width="61" height="61"><use href="#svc-chart"/></svg><span>Investment<br>and<br>Research</span></div>
      <div class="service"><svg width="61" height="61"><use href="#svc-search"/></svg><span>Performance,<br>Risk and<br>Attribution</span></div>
      <div class="service"><svg width="61" height="61"><use href="#svc-doc"/></svg><span>Finance<br>and<br>Accounting</span></div>
      <div class="service"><svg width="61" height="61"><use href="#svc-search"/></svg><span>Investment<br>and<br>Research</span></div>
      <div class="service"><svg width="61" height="61"><use href="#svc-chart"/></svg><span>Client and<br>Regulatory<br>Reporting</span></div>
      <div class="service"><svg width="61" height="61"><use href="#svc-doc"/></svg><span>Middle<br>and<br>Back Office</span></div>
    </div>
    <div class="capabilities">
      <div class="capability" style="left:40px;top:12px"><svg width="60" height="60"><use href="#cap-gear"/></svg>
        <h3>Business Strategy</h3><p>Meridian will help you create a business strategy tailored to your requirements. Ensuring each business process is defined and taken into account allows for a successful design. Creating and implementing an operating model that takes into account budget, resources, culture and your company's vision.</p></div>
      <div class="capability" style="left:355px;top:12px"><svg width="60" height="60"><use href="#cap-bulb"/></svg>
        <h3>Change management</h3><p>Meridian works with clients to deliver bespoke change initiatives. Rigorous business analysis and risk management allows for successful change initiatives. We work with you throughout the complete process, to ensure that delivery is based on value. Transition phases are challenging aspects of change initiatives which is why our team manage all transitions and the risk they carry.</p></div>
      <div class="capability" style="left:40px;top:152px"><svg width="60" height="60"><use href="#cap-laptop"/></svg>
        <h3>IT transformation</h3><p>Meridian is widely experienced in a range of technologies. We help with the implementation of software provider or design and develop bespoke services. Covering front to back office the team specialises in full project lifecycle from feasibility through to implementation.</p></div>
      <div class="capability" style="left:355px;top:152px"><svg width="60" height="60"><use href="#cap-org"/></svg>
        <h3>Organisational structure</h3><p>Meridian works with clients to improve resource capability and strategic partnerships. Acting as an extension of the HR function, we analyse business processes and ensure that our clients have the ability to manage changing workforce demands.</p></div>
    </div>
    <footer class="contact-bar">
      <span><svg width="22" height="22"><use href="#ico-phone"/></svg>+44 (0) 7700 900123</span>
      <span><svg width="22" height="22"><use href="#ico-mail"/></svg>hello@meridiank2.com</span>
      <span><svg width="22" height="22"><use href="#ico-web"/></svg>www.meridiank2.com</span>
    </footer>
  </div>
</section>

<!-- ===== Consultancy sheet, network variant ===== -->
<section class="sheet sheet--tr">
  <div class="sheet__inner">
    <svg class="hero-shapes" width="678" height="430" viewBox="0 0 678 430" aria-hidden="true">
      <polygon points="238,0 678,0 678,226 566,428" fill="var(--brand-dark)"/>
      <polygon points="600,413 678,413 678,300" fill="var(--brand-light)"/>
      <polygon points="0,138 330,138 440,282 0,282" fill="var(--brand)"/>
    </svg>
    <div class="hero-photo hero-photo--network" role="img" aria-label="Glowing digital network of connected device icons on a dark blue background"></div>
    <div class="brand-name">MERIDIAN K2</div>
    <p class="tagline"><span>A partner who brings new and</span><span>innovative ideas to the table, through</span><span>extensive industry experience and</span><span>knowledge. Meridian will ensure you are</span><span>prepared for growth.</span></p>
    <h2 class="section-title" style="top:296px">MERIDIAN CONSULTANCY</h2>
    <div class="intro" style="top:316px">
      <p>Meridian K2 is a bespoke consultancy firm that specialises in buy side investment. Through an industry based consultative approach we assist our clients in preparing for, and facilitating, long term growth. Working closely with our clients we combine innovative thinking and breakthrough technologies to accelerate progress and, together, achieve enduring results.</p>
      <p>Experienced in successfully delivering change for global organisations as well as assisting smaller firms during their growth phase. Meridian will work with you create a workable model and ensure successful delivery of the project.</p>
    </div>
    <div class="service-grid" style="top:431px">
      <div class="service"><svg width="61" height="61"><use href="#svc-doc"/></svg><span>Order<br>Management<br>and Trading</span></div>
      <div class="service"><svg width="61" height="61"><use href="#svc-doc"/></svg><span>CRM/ Onboarding</span></div>
      <div class="service"><svg width="61" height="61"><use href="#svc-doc"/></svg><span>Compliance</span></div>
      <div class="service"><svg width="61" height="61"><use href="#svc-chart"/></svg><span>Investment<br>and<br>Research</span></div>
      <div class="service"><svg width="61" height="61"><use href="#svc-search"/></svg><span>Performance,<br>Risk and<br>Attribution</span></div>
      <div class="service"><svg width="61" height="61"><use href="#svc-doc"/></svg><span>Finance<br>and<br>Accounting</span></div>
      <div class="service"><svg width="61" height="61"><use href="#svc-search"/></svg><span>Investment<br>and<br>Research</span></div>
      <div class="service"><svg width="61" height="61"><use href="#svc-chart"/></svg><span>Client and<br>Regulatory<br>Reporting</span></div>
      <div class="service"><svg width="61" height="61"><use href="#svc-doc"/></svg><span>Middle<br>and<br>Back Office</span></div>
    </div>
    <div class="capabilities">
      <div class="capability" style="left:40px;top:12px"><svg width="60" height="60"><use href="#cap-gear"/></svg>
        <h3>Business Strategy</h3><p>Meridian will help you create a business strategy tailored to your requirements. Ensuring each business process is defined and taken into account allows for a successful design. Creating and implementing an operating model that takes into account budget, resources, culture and your company's vision.</p></div>
      <div class="capability" style="left:355px;top:12px"><svg width="60" height="60"><use href="#cap-bulb"/></svg>
        <h3>Change management</h3><p>Meridian works with clients to deliver bespoke change initiatives. Rigorous business analysis and risk management allows for successful change initiatives. We work with you throughout the complete process, to ensure that delivery is based on value. Transition phases are challenging aspects of change initiatives which is why our team manage all transitions and the risk they carry.</p></div>
      <div class="capability" style="left:40px;top:152px"><svg width="60" height="60"><use href="#cap-laptop"/></svg>
        <h3>IT transformation</h3><p>Meridian is widely experienced in a range of technologies. We help with the implementation of software provider or design and develop bespoke services. Covering front to back office the team specialises in full project lifecycle from feasibility through to implementation.</p></div>
      <div class="capability" style="left:355px;top:152px"><svg width="60" height="60"><use href="#cap-org"/></svg>
        <h3>Organisational structure</h3><p>Meridian works with clients to improve resource capability and strategic partnerships. Acting as an extension of the HR function, we analyse business processes and ensure that our clients have the ability to manage changing workforce demands.</p></div>
    </div>
    <footer class="contact-bar">
      <span><svg width="22" height="22"><use href="#ico-phone"/></svg>+44 (0) 7700 900123</span>
      <span><svg width="22" height="22"><use href="#ico-mail"/></svg>hello@meridiank2.com</span>
      <span><svg width="22" height="22"><use href="#ico-web"/></svg>www.meridiank2.com</span>
    </footer>
  </div>
</section>

<!-- ===== Recruitment sheet, city variant ===== -->
<section class="sheet sheet--bl">
  <div class="sheet__inner">
    <svg class="hero-shapes" width="678" height="430" viewBox="0 0 678 430" aria-hidden="true">
      <polygon points="238,0 678,0 678,226 566,428" fill="var(--brand-dark)"/>
      <polygon points="600,413 678,413 678,300" fill="var(--brand-light)"/>
      <polygon points="0,146 330,146 440,288 0,288" fill="var(--brand)"/>
    </svg>
    <div class="hero-photo hero-photo--city" role="img" aria-label="Upward view of glass office skyscrapers against a blue sky"></div>
    <div class="brand-name">MERIDIAN K2</div>
    <p class="tagline" style="top:162px"><span>A partner who brings new and</span><span>innovative ideas to the table, through</span><span>extensive industry experience and</span><span>knowledge. Meridian will ensure you are</span><span>prepared for growth.</span></p>
    <h2 class="section-title" style="top:306px">MERIDIAN RECRUITMENT</h2>
    <div class="recruit-intro">
      <p>Meridian is more than an ordinary recruitment service. Our experts work with clients to develop a HR strategy that maps current, and impending, organisational needs; using research to effectively benchmark. We are developing various talent communities that provide effective, and timely, recruitment solutions for our clients.</p>
      <p><span class="lead">Specialists in:</span> Asset Management recruitment with a specialisation in I.T, Operations, Regulation and Change Management.</p>
    </div>
    <div class="recruit-col recruit-col--left">
      <p>Meridian acts as an extension of your HR function, providing an end-to-end permanent and contingent talent acquisition solution, taking full accountability and ownership for the entire recruitment process, which includes:</p>
      <ul class="ticks"><li>Workforce Planning</li><li>Strategic Sourcing</li><li>Talent Engagement</li><li>Candidate Management</li><li>Weekly vacancy updates</li></ul>
    </div>
    <div class="recruit-col recruit-col--right">
      <p>We recognise that hiring can be a lengthy process, therefore we partner with you to ensure you only interview top quantile candidates, cutting out multiple meetings with multiple candidates. Giving hiring managers time back in their diaries to do their day jobs and reducing the time to hire. This is achieved by:</p>
      <ul class="ticks ticks--pairs"><li>Understanding the roles, and partnering with you to build meaningful job descriptions</li><li>Support with interviews and we ensure the candidate has a positive experience</li><li>Candidates are fully screened and interviewed prior to presentation to you</li><li>Qualified shortlist of top 3 candidates</li></ul>
    </div>
    <p class="recruit-close">Meridian recruitment partners with principal business consultants from Meridian consultancy to ensure candidates are properly screened before presenting to our clients. This allows for our clients to focus on only interviewing the best on the market.</p>
    <div class="service-grid" style="top:688px">
      <div class="service"><svg width="61" height="61"><use href="#svc-doc"/></svg><span>Order<br>Management<br>and Trading</span></div>
      <div class="service"><svg width="61" height="61"><use href="#svc-doc"/></svg><span>CRM/ Onboarding</span></div>
      <div class="service"><svg width="61" height="61"><use href="#svc-doc"/></svg><span>Compliance</span></div>
      <div class="service"><svg width="61" height="61"><use href="#svc-chart"/></svg><span>Investment<br>and<br>Research</span></div>
      <div class="service"><svg width="61" height="61"><use href="#svc-search"/></svg><span>Performance,<br>Risk and<br>Attribution</span></div>
      <div class="service"><svg width="61" height="61"><use href="#svc-doc"/></svg><span>Finance<br>and<br>Accounting</span></div>
      <div class="service"><svg width="61" height="61"><use href="#svc-search"/></svg><span>Investment<br>and<br>Research</span></div>
      <div class="service"><svg width="61" height="61"><use href="#svc-chart"/></svg><span>Client and<br>Regulatory<br>Reporting</span></div>
      <div class="service"><svg width="61" height="61"><use href="#svc-doc"/></svg><span>Middle<br>and<br>Back Office</span></div>
    </div>
    <footer class="contact-bar">
      <span><svg width="22" height="22"><use href="#ico-phone"/></svg>+44 (0) 7700 900123</span>
      <span><svg width="22" height="22"><use href="#ico-mail"/></svg>hello@meridiank2.com</span>
      <span><svg width="22" height="22"><use href="#ico-web"/></svg>www.meridiank2.com</span>
    </footer>
  </div>
</section>

<!-- ===== Recruitment sheet, network variant ===== -->
<section class="sheet sheet--br">
  <div class="sheet__inner">
    <svg class="hero-shapes" width="678" height="430" viewBox="0 0 678 430" aria-hidden="true">
      <polygon points="238,0 678,0 678,226 566,428" fill="var(--brand-dark)"/>
      <polygon points="600,413 678,413 678,300" fill="var(--brand-light)"/>
      <polygon points="0,146 330,146 440,288 0,288" fill="var(--brand)"/>
    </svg>
    <div class="hero-photo hero-photo--network" role="img" aria-label="Glowing digital network of connected device icons on a dark blue background"></div>
    <div class="brand-name">MERIDIAN K2</div>
    <p class="tagline" style="top:162px"><span>A partner who brings new and</span><span>innovative ideas to the table, through</span><span>extensive industry experience and</span><span>knowledge. Meridian will ensure you are</span><span>prepared for growth.</span></p>
    <h2 class="section-title" style="top:306px">MERIDIAN RECRUITMENT</h2>
    <div class="recruit-intro">
      <p>Meridian is more than an ordinary recruitment service. Our experts work with clients to develop a HR strategy that maps current, and impending, organisational needs; using research to effectively benchmark. We are developing various talent communities that provide effective, and timely, recruitment solutions for our clients.</p>
      <p><span class="lead">Specialists in:</span> Asset Management recruitment with a specialisation in I.T, Operations, Regulation and Change Management.</p>
    </div>
    <div class="recruit-col recruit-col--left">
      <p>Meridian acts as an extension of your HR function, providing an end-to-end permanent and contingent talent acquisition solution, taking full accountability and ownership for the entire recruitment process, which includes:</p>
      <ul class="ticks"><li>Workforce Planning</li><li>Strategic Sourcing</li><li>Talent Engagement</li><li>Candidate Management</li><li>Weekly vacancy updates</li></ul>
    </div>
    <div class="recruit-col recruit-col--right">
      <p>We recognise that hiring can be a lengthy process, therefore we partner with you to ensure you only interview top quantile candidates, cutting out multiple meetings with multiple candidates. Giving hiring managers time back in their diaries to do their day jobs and reducing the time to hire. This is achieved by:</p>
      <ul class="ticks ticks--pairs"><li>Understanding the roles, and partnering with you to build meaningful job descriptions</li><li>Support with interviews and we ensure the candidate has a positive experience</li><li>Candidates are fully screened and interviewed prior to presentation to you</li><li>Qualified shortlist of top 3 candidates</li></ul>
    </div>
    <p class="recruit-close">Meridian recruitment partners with principal business consultants from Meridian consultancy to ensure candidates are properly screened before presenting to our clients. This allows for our clients to focus on only interviewing the best on the market.</p>
    <div class="service-grid" style="top:688px">
      <div class="service"><svg width="61" height="61"><use href="#svc-doc"/></svg><span>Order<br>Management<br>and Trading</span></div>
      <div class="service"><svg width="61" height="61"><use href="#svc-doc"/></svg><span>CRM/ Onboarding</span></div>
      <div class="service"><svg width="61" height="61"><use href="#svc-doc"/></svg><span>Compliance</span></div>
      <div class="service"><svg width="61" height="61"><use href="#svc-chart"/></svg><span>Investment<br>and<br>Research</span></div>
      <div class="service"><svg width="61" height="61"><use href="#svc-search"/></svg><span>Performance,<br>Risk and<br>Attribution</span></div>
      <div class="service"><svg width="61" height="61"><use href="#svc-doc"/></svg><span>Finance<br>and<br>Accounting</span></div>
      <div class="service"><svg width="61" height="61"><use href="#svc-search"/></svg><span>Investment<br>and<br>Research</span></div>
      <div class="service"><svg width="61" height="61"><use href="#svc-chart"/></svg><span>Client and<br>Regulatory<br>Reporting</span></div>
      <div class="service"><svg width="61" height="61"><use href="#svc-doc"/></svg><span>Middle<br>and<br>Back Office</span></div>
    </div>
    <footer class="contact-bar">
      <span><svg width="22" height="22"><use href="#ico-phone"/></svg>+44 (0) 7700 900123</span>
      <span><svg width="22" height="22"><use href="#ico-mail"/></svg>hello@meridiank2.com</span>
      <span><svg width="22" height="22"><use href="#ico-web"/></svg>www.meridiank2.com</span>
    </footer>
  </div>
</section>

</body>
</html>
```